A unique communication angle to crowdfunding

Looking for a fresh redesign of a crowd funding website that deals in real estate. I already have the content, but am looking to take the design to the next level.

Existing real estate crowd funding sites focus on the real estate. I want to explore communication angle that:
- puts the investor in the centre of the communication: "become a baron"
- highlights the international nature (international properties, international investors)

There's also quite a lot of copy on the site, as we need to explain the service in quite a bit of detail. There's room to reduce the copy and replace with graphics. Could also consider clicking to see different text (see our difference section in http://galleonfairs.com)

The backend of the platform is already being worked on by a specialist crowd funding service provider.

In total there are 5 pages to be designed.

The homepage is really important. Right now it looks quite dated. It doesn't have a great layout. Note there is no mobile version of the website, so the pages need to be seen well on mobile devices. When looking at the brief, refer to the following links too:

current website:
http://pennyduke.com

some revisions made so far:
http://preview.stakeharbor.com/7K3LQ9

Attached are logo files and another file which contained copy for the pages. No need to rework the logo.

Please make sure to use the same copy in the brief on the webpages, to ensure the layouts work. Designers are free to propose images they feel work on the pages.

I would like to see if rather than tweaking the pages, it's possible to come up with a better design concept. If the 5 pages are accepted, there's a chance I'll request an additional 4 pages.
Updates

Please note the font used in the logo is called "harabara" in case you decide to use it in any of the titles, etc.

Please note there is one additional page for which we would like to review designs. Note the page would be a template to be used on all future real estate detail pages. Here is an example of the current design for reference:

http://pennyduke.com/projects/view/14

In total there are 5 page designs required, (homepage + 4)

Thank you

FYI -

Just a quick note to give information from similar UK real estate crowdfunding sites:
http://www.housewalrus.co.uk
http://tiderock.co.uk
https://www.fundquarry.com

Of the above, only tiderock has a nice clean looking landing page. Information is clear and well laid out.

Hi all, just uploaded a new file in the brief. Contains some comments and a website reference. I thought it may help to explain how we could convey international aspect as well as how we could convey images in a more modern way. This is an option you can consider, but its entirely up to you how how answer the brief. Thanks!

Reason: As requested by some designers needing more time to complete their work. Continue to share your work in progress and receive timely feedback before the deadline.

We would like to let you know that we have just shortlisted the best designs. Together with that, we have also passed some detailed feedback to all designers who weren't shortlisted. If we didn't contact you, please let us know. If you haven't submitted a design or are working on revisions, please note these will no longer be taken into account now. We hope you understand that we need to close the project today. Thank you all once again for your great work and design concepts. Here's hoping we meet again on a future design brief. Cheers, pennyduke team.

Target Market(s)

At the moment, only rich are able to buy real estate. With this service, anyone can become a landlord. Target buyers:

Young professionals, looking to diversify from stock market and lower risk
People nearing retirement, looking for stable rental incomes
Retirees - looking to supplement pensions with possibility of capital gains
Parents - looking for a way to save long term for their children (instead of low interest paying bank accounts)

Industry/Entity Type

Communication

Font styles to use
Sans Serif
Other font styles liked:
• harabara

Colors
add136
f5f9eb
959595
000000

Requirements
Must have
• Overall, the site must convey "whoever you are, you too can become a landlord", and that you don't need to be wealthy to invest in real estate. See

Communication should put the investor (or the baron) at the centre. The investor can be any of those described in the target market.

Show the aspirational side of property ownership.

In addition to the investor/baron character, the second main theme is international. No other real estate crowdfunding website highlights this.
Nice to have
• Banner could show different consumer types, to illustrate that the service can appeal to many different profiles. Refer to attached file "home page reference - plainasbread.com" as an example of how this could be done.

Aim to show the international side of the service. Properties around the world, investors around the world.

```html
<!DOCTYPE html>
<html lang="en">
<head>
<meta charset="utf-8">
<title>pennyduke – Become a property baron</title>
<link rel="stylesheet" href="https://fonts.googleapis.com/css2?family=Open+Sans:wght@400;600;700&display=swap">
<style>
:root{
  --green:#add136;
  --green-pale:#f5f9eb;
  --green-soft:#eef5d6;
  --grey:#959595;
  --grey-light:#e9e9e9;
  --grey-line:#d8d8d8;
  --ink:#333333;
  --black:#000000;
  --dark:#232323;
  --footer:#2b2b2b;
  --sky:#c3e1f3;
  --white:#ffffff;
}
*{box-sizing:border-box;margin:0;padding:0}
html,body{width:1200px;height:3130px;overflow:hidden;background:var(--white);font-family:"Open Sans",Arial,sans-serif;color:var(--ink)}
.page{position:relative;width:1200px;height:3130px;overflow:hidden}
.abs{position:absolute}
.center{text-align:center;left:0;width:1200px}

/* header */
.site-header{top:0;left:0;width:1200px;height:144px;border-bottom:2px solid var(--grey-line)}
.brand{left:100px;top:48px;display:flex;align-items:center;gap:12px}
.brand-mark{width:46px;height:46px;border-radius:50%;background:var(--green)}
.brand-name{font-size:34px;font-weight:700;color:var(--green);letter-spacing:-.5px}
.social{display:flex;gap:10px}
.social span{width:26px;height:26px;border-radius:50%;background:var(--green);display:block}
.header-social{left:756px;top:44px}
.search{left:902px;top:40px;width:196px;height:32px;border:1px solid var(--grey-line);border-radius:3px;font-size:13px;color:var(--grey);padding:7px 12px}
.search svg{position:absolute;right:8px;top:7px}
.main-nav{top:116px;left:470px;display:flex;gap:30px;font-size:14px;color:#555}
.main-nav a{color:inherit;text-decoration:none;padding-bottom:12px}
.main-nav a.active{color:var(--green);border-bottom:3px solid var(--green)}

/* hero */
.hero{top:150px;left:0;width:1200px;height:503px;background:var(--sky)}
.hero-art{left:175px;top:38px;width:350px;height:380px;border-radius:8px;background:linear-gradient(160deg,#8fb8d8,#5a87b3 55%,#e8d6b8)}
.hero-title{left:582px;top:100px;width:500px;font-size:33px;line-height:44px;color:#333;font-weight:400}
.btn-light{left:584px;top:250px;background:var(--white);color:#333;font-size:15px;padding:8px 16px;border-radius:3px}
.hero-arrow{top:235px;width:38px;height:38px;border-radius:50%;background:rgba(120,140,160,.45)}
.hero-arrow svg{position:absolute;left:11px;top:10px}
.hero-city{left:0;top:424px;width:1200px;height:79px;background:linear-gradient(180deg,rgba(151,170,190,0) 0,#9bb0c4 35%,#8aa0b6 100%)}

/* intro */
.section-title{font-size:30px;color:var(--green);font-weight:400}
.body-text{font-size:15.5px;line-height:26px;color:#777}
.intro-title{top:696px}
.intro-text{top:746px;left:150px;width:900px;text-align:center}

/* split */
.split{top:887px;height:305px;width:600px}
.split-left{left:0;background:var(--green)}
.split-right{left:600px;background:var(--dark)}
.split h2{position:absolute;font-size:40px;font-weight:700;color:var(--white)}
.split p{position:absolute;color:var(--white);font-size:17px;font-weight:600;line-height:26px}
.split .sub{font-size:15px;font-weight:600;color:#f3f8e0}
.btn-dark{background:#333;color:#fff;font-size:17px;padding:10px 18px;border-radius:3px;font-weight:600}
.btn-green{background:var(--green);color:#111;font-size:17px;padding:10px 18px;border-radius:3px;font-weight:600}

/* projects */
.projects-title{top:1248px}
.projects-text{top:1298px;left:280px;width:640px;text-align:center;font-size:15px;line-height:24px;color:#777}
.card{top:1382px;width:313px;height:407px;border:1px solid var(--grey-line);background:#fff}
.card-price{height:52px;background:var(--green);color:#fff;font-size:21px;text-align:center;line-height:52px;font-weight:600}
.card-photo{height:146px}
.card-name{position:absolute;top:214px;left:0;width:100%;text-align:center;color:var(--green);font-size:17px;font-weight:400}
.card-desc{position:absolute;top:246px;left:28px;right:28px;text-align:center;font-size:12px;line-height:19px;color:#888}
.progress{position:absolute;top:326px;left:20px;right:20px;height:8px;border-radius:4px;background:#e6e6e6;overflow:hidden}
.progress span{display:block;height:100%;background:var(--green)}
.funded{position:absolute;top:341px;left:20px;font-size:13px;color:#555}
.btn-view{position:absolute;left:84px;top:381px;width:144px;height:42px;line-height:42px;text-align:center;background:#333;color:#fff;font-size:17px;border-radius:3px}

/* newsletter */
.newsletter{top:1878px;left:0;width:1200px;height:178px;background:var(--grey-light)}
.newsletter h2{position:absolute;top:22px;width:1200px;text-align:center;font-size:30px;font-weight:400;color:#333}
.newsletter p{position:absolute;top:70px;width:1200px;text-align:center;font-size:12.5px;color:#555}
.email-field{left:414px;top:104px;width:270px;height:40px;background:#fff;border:1px solid var(--grey-line);font-size:13px;color:#999;padding:11px 12px}
.btn-submit{left:693px;top:104px;width:94px;height:40px;background:#555;color:#fff;font-size:15px;font-weight:700;text-align:center;line-height:40px;border-radius:3px}

/* community */
.community-title{top:2102px}
.community-text{top:2148px;left:200px;width:800px;text-align:center;font-size:15px;color:#777}
.stat{top:2212px;width:214px;height:80px;background:var(--green-soft);text-align:center;padding-top:4px}
.stat b{font-size:36px;color:var(--green);font-weight:700}
.stat em{font-style:normal;font-size:14px;color:var(--green)}
.stat small{display:block;font-size:13px;color:var(--green);margin-top:-4px}
.stat-caption{top:2305px;width:240px;text-align:center;font-size:16px;line-height:23px;color:#222}
.press{top:2410px;left:121px;width:958px;height:140px;border:1px solid var(--grey-line)}
.press-label{position:absolute;left:14px;top:10px;font-size:11px;font-style:italic;color:#555}
.press-badge{position:absolute;height:26px;background:#9a9a9a;border-radius:2px}

/* legal */
.legal{top:2619px;left:0;width:1200px;height:366px;background:var(--grey-light)}
.legal-city{left:0;top:2860px;width:1200px;height:125px;background:linear-gradient(180deg,rgba(176,176,176,0),#b5b5b5 45%,#a9a9a9)}
.legal-box{left:125px;width:956px;background:#fff;padding:16px 20px;font-size:13px;line-height:21px;color:#8a8a8a;overflow:hidden}

/* footer */
.site-footer{top:2985px;left:0;width:1200px;height:145px;background:var(--footer)}
.footer-nav{top:3014px;width:1200px;display:flex;justify-content:center;gap:28px;font-size:13px;color:#ccc}
.copyright{left:100px;top:3082px;font-size:13px;color:#bbb}
.footer-social{left:798px;top:3078px}
.footer-social span{background:#777}
.group-badge{left:942px;top:3068px;width:160px;height:46px;background:#777}
</style>
</head>
<body>
<div class="page">

  <header class="abs site-header">
    <div class="abs brand"><span class="brand-mark"></span><span class="brand-name">pennyduke</span></div>
    <div class="abs social header-social"><span></span><span></span><span></span><span></span></div>
    <div class="abs search">Search
      <svg width="16" height="16" viewBox="0 0 16 16"><circle cx="6.5" cy="6.5" r="5" fill="none" stroke="#777" stroke-width="1.6"/><line x1="10.3" y1="10.3" x2="15" y2="15" stroke="#777" stroke-width="1.8"/></svg>
    </div>
    <nav class="abs main-nav">
      <a class="active">Home</a><a>Sign In</a><a>How It Works</a><a>Discover A Project</a><a>The Baron Blog</a><a>Find Out More</a>
    </nav>
  </header>

  <section class="abs hero">
    <div class="abs hero-art" role="img" aria-label="Illustration of a hand holding a cluster of city buildings with for-sale signs"></div>
    <h1 class="abs hero-title">Proin convallis sapien a massa pretium aliquam gravida laoreet ligula in convallis.</h1>
    <div class="abs btn-light">Read more</div>
    <div class="abs hero-arrow" style="left:28px"><svg width="16" height="18"><polyline points="11,2 4,9 11,16" fill="none" stroke="#fff" stroke-width="3"/></svg></div>
    <div class="abs hero-arrow" style="left:1132px"><svg width="16" height="18"><polyline points="5,2 12,9 5,16" fill="none" stroke="#fff" stroke-width="3"/></svg></div>
    <div class="abs hero-city" role="img" aria-label="City skyline silhouette"></div>
  </section>

  <h2 class="abs center section-title intro-title">Pennyduke is reconstructing a property ladder that's strong and fair</h2>
  <div class="abs body-text intro-text">
    <p>By harnessing the power of crowds, it's possible to become a landlord in attractive locations around the world without the burden of financing 100% of the purchase. Leave the day to day management of your property portfolio to us.</p>
    <p style="margin-top:12px">Start with as little as 1% in a project and plan your steps to becoming a true baron.</p>
  </div>

  <section class="abs split split-left">
    <svg class="abs" style="left:464px;top:30px" width="100" height="92" viewBox="0 0 100 92"><rect x="4" y="4" width="92" height="84" fill="none" stroke="#333" stroke-width="8"/><g fill="#333"><rect x="20" y="20" width="16" height="14"/><rect x="42" y="20" width="16" height="14"/><rect x="64" y="20" width="16" height="14"/><rect x="20" y="42" width="16" height="14"/><rect x="42" y="42" width="16" height="14"/><rect x="64" y="42" width="16" height="14"/><rect x="42" y="64" width="16" height="24"/></g></svg>
    <h2 style="left:110px;top:98px">Find Properties</h2>
    <p style="left:112px;top:154px">Sign up to browse the portfolio.</p>
    <p class="sub" style="left:112px;top:180px">Your journey to becoming a real estate baron starts here.</p>
    <div class="abs btn-dark" style="left:114px;top:226px">Become a Member</div>
  </section>

  <section class="abs split split-right">
    <svg class="abs" style="left:348px;top:20px" width="150" height="110" viewBox="0 0 150 110"><g fill="#fff"><circle cx="38" cy="38" r="16"/><path d="M10 100 q0-42 28-42 q28 0 28 42z"/><circle cx="112" cy="38" r="16"/><path d="M84 100 q0-42 28-42 q28 0 28 42z"/><circle cx="75" cy="30" r="20"/><path d="M40 104 q0-52 35-52 q35 0 35 52z" stroke="#232323" stroke-width="4"/></g></svg>
    <h2 style="left:32px;top:98px">Find Buyers</h2>
    <p style="left:34px;top:154px;width:420px">Submit a property or development and raise funds from our real estate barons.</p>
    <div class="abs btn-green" style="left:38px;top:226px">Submit Your Project</div>
  </section>

  <h2 class="abs center section-title projects-title">Featured Projects</h2>
  <p class="abs projects-text">Brief details of new and popular projects. To view full listings, you will be required to sign up and become a member.</p>

  <article class="abs card" style="left:100px">
    <div class="card-price">From GBP 3,600</div>
    <div class="card-photo" role="img" aria-label="Photo of a waterfront city skyline" style="background:linear-gradient(180deg,#cfe6f5,#7fa9c9 60%,#3f7fb0)"></div>
    <h3 class="card-name">14 Harbour Row London E1</h3>
    <p class="card-desc">Class aptent taciti sociosqu ad litora torquent per conubia nostra, per inceptos himenaeos. Donec ac sem id lorem ultrices.</p>
    <div class="progress"><span style="width:0"></span></div>
    <p class="funded">0% &nbsp;funded</p>
    <div class="btn-view">View more</div>
  </article>

  <article class="abs card" style="left:445px">
    <div class="card-price">From GBP 3,600</div>
    <div class="card-photo" role="img" aria-label="Photo of a brick and stone shopfront building" style="background:linear-gradient(180deg,#b9d3ea,#8a6a52 45%,#9a9a9a)"></div>
    <h3 class="card-name">14 Harbour Row London E1</h3>
    <p class="card-desc">Class aptent taciti sociosqu ad litora torquent per conubia nostra, per inceptos himenaeos. Donec ac sem id lorem ultrices.</p>
    <div class="progress"><span style="width:6%"></span></div>
    <p class="funded">4% &nbsp;funded</p>
    <div class="btn-view">View more</div>
  </article>

  <article class="abs card" style="left:787px">
    <div class="card-price">From GBP 3,600</div>
    <div class="card-photo" role="img" aria-label="Photo of a Mediterranean-style apartment complex" style="background:linear-gradient(180deg,#9cc3e4,#c7a07c 45%,#8b6a4e)"></div>
    <h3 class="card-name">14 Harbour Row London E1</h3>
    <p class="card-desc">Class aptent taciti sociosqu ad litora torquent per conubia nostra, per inceptos himenaeos. Donec ac sem id lorem ultrices.</p>
    <div class="progress"><span style="width:51%"></span></div>
    <p class="funded">51% &nbsp;funded</p>
    <div class="btn-view">View more</div>
  </article>

  <section class="abs newsletter">
    <h2>Get In Touch</h2>
    <p>sign up to receive additional information on new projects and get the newsletter</p>
    <div class="abs email-field">E-mail Address</div>
    <div class="abs btn-submit">SUBMIT</div>
  </section>

  <h2 class="abs center section-title community-title">Be Part of a Growing International Community</h2>
  <p class="abs community-text">Gain access to new projects in world class cities and join our growing community of international landlords.</p>

  <div class="abs stat" style="left:167px"><b>3,200</b><em>investors</em><small>in 6 countrie</small></div>
  <div class="abs stat" style="left:497px"><b>2,800</b><em>investors</em><small>in 6 countrie</small></div>
  <div class="abs stat" style="left:831px"><b>1,200</b><em>investors</em><small>in 6 countrie</small></div>
  <p class="abs stat-caption" style="left:154px">A community of international property barons.</p>
  <p class="abs stat-caption" style="left:484px">Collective buying power of the pennyduke community</p>
  <p class="abs stat-caption" style="left:818px">Attractive real estate from around the world</p>

  <div class="abs press">
    <span class="press-label">Featured in</span>
    <span class="press-badge" style="left:30px;top:40px;width:122px"></span>
    <span class="press-badge" style="left:178px;top:40px;width:116px"></span>
    <span class="press-badge" style="left:330px;top:40px;width:140px"></span>
    <span class="press-badge" style="left:500px;top:36px;width:76px;height:34px"></span>
    <span class="press-badge" style="left:600px;top:36px;width:44px;height:34px"></span>
    <span class="press-badge" style="left:674px;top:40px;width:148px"></span>
    <span class="press-badge" style="left:30px;top:92px;width:60px;height:30px"></span>
    <span class="press-badge" style="left:122px;top:92px;width:130px;height:30px"></span>
    <span class="press-badge" style="left:276px;top:94px;width:360px"></span>
  </div>

  <section class="abs legal"></section>
  <div class="abs legal-city" role="img" aria-label="City skyline silhouette"></div>
  <div class="abs legal-box" style="top:2650px;height:142px">By accessing this site and any pages thereof, you agree to be bound by the terms and conditions. This website is only suitable, intended and available for professional or sophisticated, or similar investors in other jurisdictions, or those who are members of pennyduke community and familiar with, and willing to, accept the risks associated with private participation. Pennyduke does not endorse any of the projects that appear on this website, nor does it make any recommendations regarding the appropriateness of particular opportunities for any participant. Each potential participant must review and evaluate the projects in his or her own discretion and determine the suitability of participating.</div>
  <div class="abs legal-box" style="top:2809px;height:142px">This website (the "Site") is in every respect unaffiliated with any site to which it links or to any company or entity (and connected projects, investment opportunity or similar) featured on this Site, and is not meant as an endorsement of any of those companies or entities ("third parties"). Furthermore and for the avoidance of doubt, Pennyduke Limited is in no way affiliated with any third parties featured or referenced on this Site. There is no commercial relationship between Pennyduke Limited and such third parties, nor an agency arrangement or similar. If you believe your Content (including third party content) as each such term is defined in our Terms of Service has been reproduced on the Site without consent, please contact us.</div>

  <footer class="abs site-footer"></footer>
  <nav class="abs footer-nav">
    <span>• Terms of Service</span><span>• Privacy Policy</span><span>• How It Works</span><span>• Discover A Project</span><span>• The Baron Blog</span><span>• FAQ</span><span>• Contact</span>
  </nav>
  <p class="abs copyright">Copyright &nbsp;© &nbsp;2014 &nbsp;Pennyduke. &nbsp;All rights reserved.</p>
  <div class="abs social footer-social"><span></span><span></span><span></span><span></span></div>
  <div class="abs group-badge"></div>

</div>
</body>
</html>
```